The Vellmark Company Sweet Packaging Design

The Vellmark Goods Company is looking for a logo and label design for an upcoming line of honey based health and beauty products that are sourced from the Polynesian Islands (Hawaii, New Zealand, Fiji etc.).The brand will be premium price positioned and the design and packaging should exude class and quality.The design should be flexible enough to add products from future locations.We would like to see the design across three different product forms:1. Glass Honey Jar (main product)2. Hand cream / lotion (pump bottle, or lotion tube)3. Small box (e.g. throat lozenges / gum packet etc.)The Polynesia Islands are unique and exotic locations; the design/packaging should reflect this but should not be overly complicated. Each individual island has their own distinct culture and history but they have many commonalities which fall under "Polynesian Culture". The Vellmark Goods Company is an umbrella brand that should be able to support a growing number of products.Possible designs may (but are not required to) incorporate local flowers (Hawaii / Hibiscus flower, New Zealand / Manuka Flower etc.) into the design, Islands, and boutique feel (elegant classy looking)Please feel free to ask more questions for further guidance but we really want to see where the creative process can take us outside of what we have already considered internally.
Updates

We needed to modify our idea slightly because of competition.

We needed extend to get a few more ideas. We did not want to copy our competition and needed to add a part to our design that we did not include before.

Target Market(s)

Health conscious people. Honey lovers.

Font styles to use
Serif
Sans Serif
Decorative

Colors

Designer to choose colors to be used in the design.

Requirements
Must have
• a little tribal look. because its 100% polynesian Honey.. it would be nice to have the fee of that in the design..

```html
<!DOCTYPE html>
<html lang="en">
<head>
<meta charset="utf-8">
<title>The Vellmark Goods Company — Honey Labels</title>
<link rel="stylesheet" href="https://fonts.googleapis.com/css2?family=DM+Serif+Display&family=Karla:wght@400&family=Playfair+Display:wght@500&display=swap">
<style>
  :root {
    --backdrop: #e4e4e4;
    --label: #2f2f30;
    --label-deep: #262627;
    --pattern-light: #4a4a4b;
    --ink: #e9e9e9;
    --ink-soft: #d2d2d2;
  }
  * { margin: 0; padding: 0; box-sizing: border-box; }
  html, body { width: 1200px; height: 960px; overflow: hidden; }
  body {
    background: var(--backdrop);
    display: flex;
    justify-content: center;
    align-items: center;
    gap: 60px;
  }
  .label {
    position: relative;
    width: 480px;
    height: 560px;
    background: var(--label);
    overflow: hidden;
    color: var(--ink);
    text-align: center;
  }
  .label__flora {
    position: absolute;
    inset: 0;
  }
  .label--manuka .label__flora {
    background:
      radial-gradient(circle at 20% 25%, var(--pattern-light) 0, transparent 32%),
      radial-gradient(circle at 80% 30%, var(--pattern-light) 0, transparent 30%),
      radial-gradient(circle at 25% 75%, var(--pattern-light) 0, transparent 30%),
      radial-gradient(circle at 78% 78%, var(--pattern-light) 0, transparent 30%),
      var(--label-deep);
    opacity: 0.85;
  }
  .label--hibiscus .label__flora {
    background:
      radial-gradient(circle at 12% 22%, var(--pattern-light) 0, transparent 20%),
      radial-gradient(circle at 88% 22%, var(--pattern-light) 0, transparent 20%),
      radial-gradient(circle at 14% 68%, var(--pattern-light) 0, transparent 20%),
      radial-gradient(circle at 88% 66%, var(--pattern-light) 0, transparent 20%),
      radial-gradient(circle at 58% 80%, var(--pattern-light) 0, transparent 22%),
      var(--label);
    opacity: 0.8;
  }
  .label__content {
    position: relative;
    height: 100%;
    display: flex;
    flex-direction: column;
    align-items: center;
    padding-top: 52px;
  }
  .brand-seal {
    width: 180px;
    height: 180px;
    border: 3px solid var(--ink);
    border-radius: 50%;
    display: flex;
    align-items: center;
    justify-content: center;
    font-family: "Playfair Display", serif;
    font-weight: 500;
    font-size: 30px;
    color: var(--ink);
  }
  .brand-name {
    margin-top: 22px;
    font-family: "Playfair Display", serif;
    font-weight: 500;
    font-size: 15px;
    color: var(--ink-soft);
  }
  .variety {
    margin-top: 30px;
    font-family: "Karla", sans-serif;
    font-size: 15px;
    letter-spacing: 1px;
    color: var(--ink-soft);
  }
  .product {
    margin-top: 4px;
    font-family: "DM Serif Display", serif;
    font-size: 54px;
    line-height: 1.05;
    color: var(--ink);
  }
  .origin {
    margin-top: 8px;
    font-family: "Karla", sans-serif;
    font-size: 15px;
    letter-spacing: 1px;
    color: var(--ink-soft);
  }
  .volume {
    position: absolute;
    bottom: 36px;
    left: 0;
    right: 0;
    font-family: "Playfair Display", serif;
    font-weight: 500;
    font-size: 12px;
    color: var(--ink-soft);
  }
</style>
</head>
<body>
  <section class="label label--manuka">
    <div class="label__flora" role="img" aria-label="Muted grey pattern of manuka blossoms and needle-like leaves"></div>
    <div class="label__content">
      <div class="brand-seal">Vellmark</div>
      <p class="brand-name">The Vellmark Goods Company</p>
      <p class="variety">Manuka Blossom</p>
      <h2 class="product">Honey</h2>
      <p class="origin">New Zealand</p>
      <p class="volume">250 ml | 8.45 fl oz.</p>
    </div>
  </section>

  <section class="label label--hibiscus">
    <div class="label__flora" role="img" aria-label="Muted grey pattern of hibiscus flowers and leaves"></div>
    <div class="label__content">
      <div class="brand-seal">Vellmark</div>
      <p class="brand-name">The Vellmark Goods Company</p>
      <p class="variety">Hibiscus Blossom</p>
      <h2 class="product">Honey</h2>
      <p class="origin">Hawaii</p>
      <p class="volume">250 ml | 8.45 fl oz.</p>
    </div>
  </section>
</body>
</html>
```